Real Estate Webpage Design

We have an existing website: ferndaleestatecollective.com.au
We focus customised service mainly on Property Management and second-hand property sales.
We are not entirely happy about the current design and layout can stay roughly the same as the back end coding is linked to a CRM system.
We would like to see the design are more reachable to our clients and appearing.
Please check our Website Design Draft for more details.

Industry/Entity Type

Real estate Agency

Number of Pages Required

5+ page

Font styles to use
Sans Serif

Colors

Designer to choose colors to be used in the design.

```html
<!DOCTYPE html>
<html lang="en">
<head>
<meta charset="utf-8">
<title>Ferndale Estate Collective</title>
<link href="https://fonts.googleapis.com/css2?family=Poppins:wght@300;400;500;600&display=swap" rel="stylesheet">
<style>
:root{
  --gold:#f2b437;
  --gold-dark:#d99b1f;
  --navy:#1b2b47;
  --ink:#1f1f1f;
  --muted:#7b7b7b;
  --line:#e3e3e3;
  --cream:#faf0d6;
  --pale:#f5f7fb;
  --white:#fff;
}
*{box-sizing:border-box;margin:0;padding:0}
html,body{width:1200px;height:4231px;overflow:hidden}
body{font-family:'Poppins',sans-serif;color:var(--ink);background:var(--white);position:relative}
.abs{position:absolute}
.center{text-align:center}
.btn{position:absolute;background:var(--gold);color:#fff;font-size:13px;display:flex;align-items:center;justify-content:center;border:1px solid var(--gold-dark)}
.btn-outline{background:#fff;color:var(--ink);border:1px solid var(--gold)}
h2.section-title{position:absolute;left:0;width:1200px;text-align:center;font-size:27px;font-weight:500}

.site-header{position:absolute;top:0;left:0;width:1200px;height:59px;background:#fff;z-index:3}
.logo-box{position:absolute;left:60px;top:0;width:224px;height:75px;background:#fff;z-index:4}
.brand{position:absolute;display:flex;align-items:center;gap:8px}
.brand-mark{width:30px;height:30px;border:3px solid var(--gold)}
.brand-name{font-size:22px;color:var(--gold);font-weight:500;line-height:1}
.brand-sub{font-size:7px;color:var(--navy);letter-spacing:.5px}
.nav{position:absolute;top:24px;left:433px;display:flex;gap:24px;font-size:13px}
.nav a{color:var(--ink);text-decoration:none}
.nav a.active{color:var(--gold);position:relative}
.nav a.active:after{content:"";position:absolute;left:-4px;right:-4px;top:33px;height:2px;background:var(--gold)}

.hero{position:absolute;top:59px;left:0;width:1200px;height:616px;background:linear-gradient(180deg,#8aa0b8 0%,#b9c3cc 40%,#7c7568 70%,#4c5a3a 100%)}
.hero-title{position:absolute;left:61px;top:240px;font-size:38px;line-height:50px;color:var(--gold);font-weight:500}
.hero-text{position:absolute;left:61px;top:350px;width:560px;font-size:13px;line-height:23px;color:#fff}
.search{position:absolute;left:61px;top:435px;width:479px;height:51px;background:#fff;display:flex}
.search .want{width:104px;padding:8px 12px;border-right:1px solid var(--line)}
.search .loc{flex:1;padding:8px 10px}
.search small{display:block;font-size:9px;color:var(--gold)}
.search span{font-size:11px}
.search .loc span{color:var(--muted)}
.search .go{width:46px;margin:6px;background:var(--gold);display:flex;align-items:center;justify-content:center}

.feature{position:absolute;top:825px;width:260px;text-align:center}
.feature h3{font-size:16px;font-weight:500;margin-top:14px}
.feature p{font-size:12.5px;line-height:22px;color:var(--muted);margin-top:4px}
.divider{position:absolute;left:0;top:1067px;width:1200px;height:1px;background:var(--line)}

.save-card{position:absolute;top:1221px;width:260px;height:133px;background:var(--cream);text-align:center;padding-top:23px}
.save-card small{font-size:11.5px}
.save-card strong{display:block;font-size:27px;font-weight:400;margin:2px 0}
.save-card p{font-size:12.5px}
.save-card b{font-weight:600}
.tooltip{position:absolute;left:492px;top:1382px;width:122px;height:53px;border:1px solid #ccc;background:#fff;text-align:center;padding-top:8px}
.tooltip small{font-size:9px;display:block}
.tooltip strong{font-size:16px;font-weight:400}
.track{position:absolute;left:348px;top:1452px;width:527px;height:3px;background:#f4e6c4}
.track-fill{position:absolute;left:348px;top:1452px;width:205px;height:3px;background:var(--gold)}
.knob{position:absolute;left:544px;top:1444px;width:19px;height:19px;border-radius:50%;background:#fff;border:2px solid var(--gold)}
.range-label{position:absolute;top:1460px;font-size:13px;text-align:center;width:80px}

.listings{position:absolute;top:1694px;left:0;width:1200px;height:739px;background:var(--pale)}
.tabs{position:absolute;left:335px;top:1806px;display:flex}
.tabs div{width:106px;height:38px;border:1px solid #bbb;background:#fff;font-size:13px;display:flex;align-items:center;justify-content:center;position:relative}
.tabs div.on{background:var(--gold);color:#fff;border-color:var(--gold)}
.tabs div.on:after{content:"";position:absolute;bottom:-7px;left:46px;border:7px solid transparent;border-bottom:0;border-top-color:var(--gold)}
.card{position:absolute;top:1878px;width:340px;height:410px;background:#fff;box-shadow:0 2px 6px rgba(0,0,0,.08)}
.card .photo{position:absolute;left:8px;top:10px;width:324px;height:177px}
.card .badge{position:absolute;left:0;top:0;background:var(--navy);color:#fff;font-size:11px;padding:2px 7px}
.card .price{position:absolute;left:22px;top:150px;color:#fff;font-size:16px;font-weight:500}
.card .next{position:absolute;left:298px;top:150px;width:24px;height:24px;border-radius:50%;background:rgba(20,20,20,.55)}
.card h4{position:absolute;left:20px;top:193px;font-size:16px;font-weight:500}
.card .addr{position:absolute;left:20px;top:219px;font-size:13px;display:flex;gap:6px;align-items:center}
.card .feats{position:absolute;left:20px;top:252px;font-size:13px;display:flex;gap:14px;align-items:center}
.card .feats span{display:flex;gap:6px;align-items:center}
.card .insp{position:absolute;left:20px;top:291px;font-size:16px;font-weight:500}
.card .when{position:absolute;left:20px;top:319px;font-size:13px;color:var(--gold)}
.card .foot{position:absolute;left:0;top:350px;width:340px;border-top:1px solid var(--line);height:60px}
.card .avatar{position:absolute;left:18px;top:15px;width:30px;height:30px;background:#c8c4bd}
.card .agent{position:absolute;left:58px;top:20px;font-size:13px}
.card .tools{position:absolute;right:18px;top:22px;display:flex;gap:8px}
.slide-arrow{position:absolute;width:30px;height:30px;display:flex;align-items:center;justify-content:center}

.about-photo{position:absolute;top:2433px;left:0;width:1200px;height:596px;background:linear-gradient(160deg,#9fb5c8 0%,#c9d2d6 35%,#8d8f86 60%,#3e4a34 100%)}
.about-box{position:absolute;left:61px;top:2794px;width:1080px;height:432px;background:var(--cream);text-align:center}
.about-box h2{font-size:27px;font-weight:500;margin-top:50px}
.about-box p{font-size:12.5px;line-height:22px;color:var(--muted);width:660px;margin:18px auto 0}
.about-box p.note{color:var(--gold);width:720px}

.quote-text{position:absolute;left:345px;top:3412px;width:510px;text-align:center;font-size:13px;line-height:22.5px;color:var(--muted)}

.cta{position:absolute;top:3669px;left:0;width:1200px;height:228px;background:var(--navy);text-align:center;color:#fff}
.cta h2{font-size:23px;font-weight:500;line-height:38px;margin-top:46px}

.footer-col{position:absolute;top:3930px;font-size:12px;line-height:27px}
.footer-col h5{color:var(--gold);font-size:13px;font-weight:500;margin-bottom:10px}
.footer-col a{display:block;color:var(--ink);text-decoration:none;font-size:12px}
.contact-row{display:flex;gap:12px;align-items:flex-start;line-height:19px;margin-bottom:12px}
.social{display:flex;gap:14px}
.social span{width:37px;height:37px;border-radius:50%;border:2px solid var(--gold)}
.social span.fill{background:var(--gold)}
.bottom-line{position:absolute;top:4194px;left:0;width:1200px;height:1px;background:var(--line)}
.bottom{position:absolute;top:4204px;font-size:11.5px}
</style>
</head>
<body>

<header class="site-header">
  <nav class="nav">
    <a class="active" href="#">Home</a><a href="#">About Us</a><a href="#">Leasing</a><a href="#">Buy</a><a href="#">Sell</a><a href="#">Our Team</a><a href="#">Blog</a><a href="#">Contact Us</a>
  </nav>
  <div class="btn" style="left:1013px;top:18px;width:126px;height:35px">Add Properties</div>
</header>
<div class="logo-box">
  <div class="brand" style="left:20px;top:16px">
    <div class="brand-mark"></div>
    <div><div class="brand-name">Ferndale</div><div class="brand-sub">Estate Collective</div></div>
  </div>
</div>

<section class="hero" role="img" aria-label="Modern two-storey home with timber fence and garden under a cloudy sky"></section>
<h1 class="hero-title">Welcome To Ferndale<br>Estate Collective</h1>
<p class="hero-text">Lorem Ipsum is simply dummy text of the printing and typesetting industry. Lorem Ipsum has been the industry's standard dummy text ever since the 1500s, when an unknown printer</p>
<div class="search">
  <div class="want"><small>I WANT TO</small><span>Buy House</span></div>
  <div class="loc"><small>Location</small><span>Enter Street adress,city,town,zip,school district...</span></div>
  <div class="go"><svg width="18" height="18" viewBox="0 0 18 18" fill="none" stroke="#fff" stroke-width="2"><circle cx="7.5" cy="7.5" r="5.5"/><path d="M11.5 11.5l5 5"/></svg></div>
</div>

<h2 class="section-title" style="top:752px">Why People Choose Ferndale?</h2>
<div class="feature" style="left:174px">
  <svg width="64" height="60" viewBox="0 0 64 60" fill="none" stroke="#1b2b47" stroke-width="2"><circle cx="32" cy="30" r="6"/><circle cx="17" cy="34" r="5"/><circle cx="47" cy="34" r="5"/><path d="M22 56c0-9 20-9 20 0M8 56c0-8 14-8 14-4M42 52c0-4 14-4 14 4"/><path d="M32 4l2 4 4 .5-3 3 .8 4-3.8-2-3.8 2 .8-4-3-3 4-.5z" stroke="#f2b437"/><path d="M16 12l1.5 3 3 .4-2.2 2 .6 3-2.9-1.5-2.9 1.5.6-3-2.2-2 3-.4zM48 12l1.5 3 3 .4-2.2 2 .6 3-2.9-1.5-2.9 1.5.6-3-2.2-2 3-.4z" stroke="#f2b437" stroke-width="1.5"/></svg>
  <h3>Great Experience</h3>
  <p>Lorem Ipsum is simply dummy text of the printing and typesetting industry. Lorem Ipsum has been the industry's standard dummy text</p>
</div>
<div class="feature" style="left:469px">
  <svg width="64" height="60" viewBox="0 0 64 60" fill="none" stroke="#1b2b47" stroke-width="2"><rect x="20" y="4" width="24" height="26" stroke="#f2b437"/><path d="M26 10h4M34 10h4M26 16h4M34 16h4M26 22h4M34 22h4" stroke="#f2b437"/><path d="M4 34h10l8 4 10-4 10 4 8-4h10v18H50l-8 4H22l-8-4H4z"/><path d="M22 40l10 8M30 38l10 8"/></svg>
  <h3>Safety Deals</h3>
  <p>Lorem Ipsum is simply dummy text of the printing and typesetting industry. Lorem Ipsum has been the industry's standard dummy text</p>
</div>
<div class="feature" style="left:766px">
  <svg width="64" height="60" viewBox="0 0 64 60" fill="none" stroke="#1b2b47" stroke-width="2"><circle cx="30" cy="30" r="16"/><circle cx="30" cy="28" r="7"/><path d="M20 42c2-8 18-8 20 0M12 30a18 18 0 0 1 36 0"/><rect x="44" y="4" width="16" height="11" rx="2" stroke="#f2b437"/><path d="M48 15l-2 4 5-4" stroke="#f2b437"/></svg>
  <h3>Comprehensive Support</h3>
  <p>Lorem Ipsum is simply dummy text of the printing and typesetting industry. Lorem Ipsum has been the industry's standard dummy text</p>
</div>
<div class="divider"></div>

<h2 class="section-title" style="top:1148px">See How Much You Can Save</h2>
<div class="save-card" style="left:325px"><small>YOU SAVE</small><strong>$74,000</strong><p><b>Buying</b> With Ferndale</p></div>
<div class="save-card" style="left:614px"><small>YOU SAVE</small><strong>$1,41,000</strong><p><b>Buying</b> With Ferndale</p></div>
<div class="tooltip"><small>Your Home value</small><strong>$74,000</strong></div>
<svg class="abs" style="left:286px;top:1428px" width="28" height="26" viewBox="0 0 28 26" fill="none" stroke="#555" stroke-width="1.6"><path d="M2 13L14 2l12 11M6 10v14h16V10M11 24v-8h6v8"/></svg>
<svg class="abs" style="left:913px;top:1428px" width="28" height="26" viewBox="0 0 28 26" fill="none" stroke="#555" stroke-width="1.6"><path d="M2 13L14 2l12 11M6 10v14h16V10M11 24v-8h6v8"/></svg>
<div class="range-label" style="left:259px">$50,000</div>
<div class="range-label" style="left:887px">$2,00,000</div>
<div class="track"></div><div class="track-fill"></div><div class="knob"></div>
<div class="btn" style="left:491px;top:1532px;width:97px;height:33px">Sell House</div>
<div class="btn btn-outline" style="left:611px;top:1532px;width:97px;height:33px">Buy House</div>
<p class="abs center" style="left:0;top:1588px;width:1200px;font-size:13px">Have question? Call us <span style="color:var(--gold);font-size:16px;margin-left:4px">02 6230 5512</span></p>

<section class="listings"></section>
<h2 class="section-title" style="top:1740px">Listings Available For Latest Property</h2>
<div class="tabs"><div class="on">For Sale</div><div>For Lease</div><div>Open Times</div><div>Sold</div><div>Leased</div></div>

<div class="slide-arrow" style="left:15px;top:2096px;background:var(--gold)"><svg width="10" height="14" viewBox="0 0 10 14" fill="none" stroke="#fff" stroke-width="1.6"><path d="M8 1L2 7l6 6"/></svg></div>
<div class="slide-arrow" style="left:1154px;top:2096px;background:#fff;border:1px solid #999"><svg width="10" height="14" viewBox="0 0 10 14" fill="none" stroke="#333" stroke-width="1.6"><path d="M2 1l6 6-6 6"/></svg></div>

<div class="card" style="left:61px">
  <div class="photo" role="img" aria-label="Apartment tower with red balconies beside green trees" style="background:linear-gradient(135deg,#6f9fd6,#d9dde2 50%,#3f6b33)"></div>
  <div class="badge">On Sale</div>
  <div class="price">$369,900+</div><div class="next"></div>
  <h4>Gungahlin</h4>
  <div class="addr"><svg width="12" height="16" viewBox="0 0 12 16" fill="none" stroke="#f2b437" stroke-width="1.4"><path d="M6 15s5-5.5 5-9A5 5 0 0 0 1 6c0 3.5 5 9 5 9z"/><circle cx="6" cy="6" r="2"/></svg>58/12 Banksia Street Belconnen...</div>
  <div class="feats"><span><svg width="18" height="14" viewBox="0 0 18 14" fill="none" stroke="#f2b437" stroke-width="1.4"><path d="M1 13V1M1 8h16v5M4 8V5h6v3"/></svg>1</span><span><svg width="18" height="14" viewBox="0 0 18 14" fill="none" stroke="#f2b437" stroke-width="1.4"><path d="M1 7h16v2a4 4 0 0 1-4 4H5a4 4 0 0 1-4-4zM4 7V2a1.5 1.5 0 0 1 3 0"/></svg>1</span><span><svg width="22" height="14" viewBox="0 0 22 14" fill="none" stroke="#f2b437" stroke-width="1.4"><path d="M1 10V7l3-5h12l4 5v3zM5 10a2 2 0 0 0 4 0M14 10a2 2 0 0 0 4 0"/></svg>1</span></div>
  <div class="insp">Next Inspection:</div>
  <div class="when">Sat 21st May 9:40 Am-10:00 Am</div>
  <div class="foot"><div class="avatar" role="img" aria-label="Agent portrait"></div><div class="agent">Mei Tan</div>
    <div class="tools"><svg width="15" height="15" viewBox="0 0 16 16" fill="none" stroke="#333" stroke-width="1.3"><circle cx="8" cy="8" r="7"/><path d="M8 4v4l3 2"/></svg><svg width="15" height="15" viewBox="0 0 16 16" fill="none" stroke="#333" stroke-width="1.3"><path d="M1 5V1h4M11 1h4v4M15 11v4h-4M5 15H1v-4M1 1l5 5M15 1l-5 5M15 15l-5-5M1 15l5-5"/></svg><svg width="17" height="14" viewBox="0 0 18 14" fill="none" stroke="#333" stroke-width="1.3"><rect x="1" y="1" width="16" height="12"/><path d="M1 1l8 7 8-7"/></svg></div></div>
</div>
<div class="card" style="left:428px">
  <div class="photo" role="img" aria-label="High-rise apartments next to an infinity pool overlooking the city" style="background:linear-gradient(90deg,#8c8c8c 0%,#b9b5ac 40%,#a9c6e6 60%,#6a93b8 100%)"></div>
  <div class="badge">On Sale</div>
  <div class="price">$5,00,000+</div><div class="next"></div>
  <h4>Gungahlin</h4>
  <div class="addr"><svg width="12" height="16" viewBox="0 0 12 16" fill="none" stroke="#f2b437" stroke-width="1.4"><path d="M6 15s5-5.5 5-9A5 5 0 0 0 1 6c0 3.5 5 9 5 9z"/><circle cx="6" cy="6" r="2"/></svg>Level 4/22 Wattlebird Lane...</div>
  <div class="feats"><span><svg width="18" height="14" viewBox="0 0 18 14" fill="none" stroke="#f2b437" stroke-width="1.4"><path d="M1 13V1M1 8h16v5M4 8V5h6v3"/></svg>2</span><span><svg width="18" height="14" viewBox="0 0 18 14" fill="none" stroke="#f2b437" stroke-width="1.4"><path d="M1 7h16v2a4 4 0 0 1-4 4H5a4 4 0 0 1-4-4zM4 7V2a1.5 1.5 0 0 1 3 0"/></svg>2</span><span><svg width="22" height="14" viewBox="0 0 22 14" fill="none" stroke="#f2b437" stroke-width="1.4"><path d="M1 10V7l3-5h12l4 5v3zM5 10a2 2 0 0 0 4 0M14 10a2 2 0 0 0 4 0"/></svg>1</span></div>
  <div class="insp">Next Inspection:</div>
  <div class="when">Sat 21st May 9:40 Am-10:00 Am</div>
  <div class="foot"><div class="avatar" role="img" aria-label="Agent portrait"></div><div class="agent">Mei Tan</div>
    <div class="tools"><svg width="15" height="15" viewBox="0 0 16 16" fill="none" stroke="#333" stroke-width="1.3"><circle cx="8" cy="8" r="7"/><path d="M8 4v4l3 2"/></svg><svg width="15" height="15" viewBox="0 0 16 16" fill="none" stroke="#333" stroke-width="1.3"><path d="M1 5V1h4M11 1h4v4M15 11v4h-4M5 15H1v-4M1 1l5 5M15 1l-5 5M15 15l-5-5M1 15l5-5"/></svg><svg width="17" height="14" viewBox="0 0 18 14" fill="none" stroke="#333" stroke-width="1.3"><rect x="1" y="1" width="16" height="12"/><path d="M1 1l8 7 8-7"/></svg></div></div>
</div>
<div class="card" style="left:799px">
  <div class="photo" role="img" aria-label="Two-storey house with double garage and flowering tree" style="background:linear-gradient(135deg,#7aa4d6,#c7b7c4 35%,#8e8e92 65%,#4c5a45)"></div>
  <div class="badge">On Sale</div>
  <div class="price">$5,00,000+</div><div class="next"></div>
  <h4>Gungahlin</h4>
  <div class="addr"><svg width="12" height="16" viewBox="0 0 12 16" fill="none" stroke="#f2b437" stroke-width="1.4"><path d="M6 15s5-5.5 5-9A5 5 0 0 0 1 6c0 3.5 5 9 5 9z"/><circle cx="6" cy="6" r="2"/></svg>Level 4/22 Wattlebird Lane...</div>
  <div class="feats"><span><svg width="18" height="14" viewBox="0 0 18 14" fill="none" stroke="#f2b437" stroke-width="1.4"><path d="M1 13V1M1 8h16v5M4 8V5h6v3"/></svg>2</span><span><svg width="18" height="14" viewBox="0 0 18 14" fill="none" stroke="#f2b437" stroke-width="1.4"><path d="M1 7h16v2a4 4 0 0 1-4 4H5a4 4 0 0 1-4-4zM4 7V2a1.5 1.5 0 0 1 3 0"/></svg>2</span><span><svg width="22" height="14" viewBox="0 0 22 14" fill="none" stroke="#f2b437" stroke-width="1.4"><path d="M1 10V7l3-5h12l4 5v3zM5 10a2 2 0 0 0 4 0M14 10a2 2 0 0 0 4 0"/></svg>1</span></div>
  <div class="insp">Next Inspection:</div>
  <div class="when">Sat 21st May 9:40 Am-10:00 Am</div>
  <div class="foot"><div class="avatar" role="img" aria-label="Agent portrait"></div><div class="agent">Mei Tan</div>
    <div class="tools"><svg width="15" height="15" viewBox="0 0 16 16" fill="none" stroke="#333" stroke-width="1.3"><circle cx="8" cy="8" r="7"/><path d="M8 4v4l3 2"/></svg><svg width="15" height="15" viewBox="0 0 16 16" fill="none" stroke="#333" stroke-width="1.3"><path d="M1 5V1h4M11 1h4v4M15 11v4h-4M5 15H1v-4M1 1l5 5M15 1l-5 5M15 15l-5-5M1 15l5-5"/></svg><svg width="17" height="14" viewBox="0 0 18 14" fill="none" stroke="#333" stroke-width="1.3"><rect x="1" y="1" width="16" height="12"/><path d="M1 1l8 7 8-7"/></svg></div></div>
</div>
<div class="btn" style="left:550px;top:2347px;width:98px;height:32px">View More</div>

<section class="about-photo" role="img" aria-label="Modern concrete and timber house with glass walls among trees"></section>
<div class="about-box">
  <h2>Who Is Ferndale?</h2>
  <p>Ferndale is named for "the green valley, the home", buying a property is one of the most expensive expenses and important assets for people. Ferndale is a real estate company located in Gungahlin, Canberra.</p>
  <p>Being a portfolio sales agent and property manager, coupled with our high-profile international real estate experience, Ferndale is considered a market leader on the cutting edge with deep industry knowledge, ranging from landlord-tenant relationships, residential purchases.</p>
  <p class="note">FOR CONFIDENTIALITY REASONS,20 TO 30% OF OUR PROPERTIES PLEASE CALL US FOR MORE INFORMATION.</p>
  <div class="btn" style="left:500px;top:343px;width:106px;height:33px">More About</div>
</div>

<h2 class="section-title" style="top:3304px">What Our People Says</h2>
<svg class="abs" style="left:580px;top:3360px" width="40" height="34" viewBox="0 0 40 34" fill="#f2b437"><path d="M0 34V20C0 8 6 2 16 0l2 5c-6 2-9 6-9 11h8v18zM22 34V20c0-12 6-18 16-20l2 5c-6 2-9 6-9 11h8v18z"/></svg>
<p class="quote-text">I would highly recommend Ferndale property to you, they were helping me manage my investment property, they found a quality tenant in 2 days and maintain my property in a really good condition, they will update everything with me all the time and settle my worries. Claire, who is my PM, she is very patient and professional. I have had a bad property management experience, hence, I have had lots worries and questions, but Claire gained my trust and has done a really good job.</p>
<p class="abs center" style="left:0;width:1200px;top:3574px;font-size:13px">Lia Ren</p>
<div class="slide-arrow" style="left:211px;top:3468px;width:36px;height:36px;background:var(--gold)"><svg width="10" height="16" viewBox="0 0 10 16" fill="none" stroke="#fff" stroke-width="1.6"><path d="M8 1L2 8l6 7"/></svg></div>
<div class="slide-arrow" style="left:937px;top:3468px;width:36px;height:36px;background:#fff;border:1px solid #999"><svg width="10" height="16" viewBox="0 0 10 16" fill="none" stroke="#333" stroke-width="1.6"><path d="M2 1l6 7-6 7"/></svg></div>

<section class="cta">
  <h2>Contact Us If You Want To Sell Your House Or You<br>Have Other Questions</h2>
  <div class="btn" style="left:496px;top:140px;width:208px;height:34px">Request Free Consultation</div>
</section>

<footer>
  <div class="brand" style="left:61px;top:3938px">
    <div class="brand-mark" style="width:40px;height:40px"></div>
    <div><div class="brand-name" style="font-size:30px">Ferndale</div><div class="brand-sub">Estate Collective</div></div>
  </div>
  <p class="abs" style="left:61px;top:4004px;width:200px;font-size:12px;line-height:22px">Lorem ipsum dolor sit amet, consectetur adipiscing elit, sed do eiusmod tempor...</p>
  <div class="footer-col" style="left:332px;line-height:27px">
    <h5>Site Map</h5>
    <a href="#">Home</a><a href="#">About Us</a><a href="#">Leasing</a><a href="#">Buy</a><a href="#">Sell</a><a href="#">Our Team</a><a href="#">Blog</a><a href="#">Contact Us</a>
  </div>
  <div class="footer-col" style="left:612px">
    <h5>Contact Us</h5>
    <div class="contact-row"><svg width="20" height="22" viewBox="0 0 20 22" fill="none" stroke="#333" stroke-width="1.4"><path d="M10 17s6-6 6-10A6 6 0 0 0 4 7c0 4 6 10 6 10z"/><circle cx="10" cy="7" r="2"/><path d="M5 15l-4 6h18l-4-6"/></svg><span>18/7 Wattlebird Lane,<br>Gungahlin, ACT, 2912</span></div>
    <div class="contact-row"><svg width="20" height="20" viewBox="0 0 20 20" fill="none" stroke="#333" stroke-width="1.4"><path d="M4 1l4 4-2 3c1 3 3 5 6 6l3-2 4 4-3 3C8 19 1 12 1 4z"/></svg><span style="font-weight:600">02 6230 5512<br>02 6230 5519</span></div>
    <div class="contact-row"><svg width="20" height="16" viewBox="0 0 20 16" fill="none" stroke="#333" stroke-width="1.4"><rect x="1" y="1" width="18" height="14"/><path d="M1 1l9 8 9-8"/></svg><span>hello@ferndaleestate.com</span></div>
  </div>
  <div class="footer-col" style="left:888px">
    <h5>Follow On Us</h5>
    <div class="social"><span class="fill"></span><span></span><span></span><span></span></div>
  </div>
  <div class="bottom-line"></div>
  <p class="bottom" style="left:61px">2022© Ferndale Properties. All right reserved.</p>
  <p class="bottom" style="left:655px;word-spacing:1px">Privacy &nbsp;&nbsp;&nbsp;&nbsp; Complaint Handling &amp; Dispute Resolution &nbsp;&nbsp;&nbsp;&nbsp; Due Diligence Checklist</p>
</footer>

</body>
</html>
```